Business Card Re-Design/Update

We'd like to update out business cards. I've included our current "Style guide" which has the colour scheme of the organisation in it. I've also included the branding files with logos etc in them.

I've also included a copy of one of our existing cards so that you can see how ugly/dated they look. I'd like a fresh modern corporate look.

Target Market(s)

These are for our clients, potential clients, industry contacts - like all business cards

Contact Information for Business Card

Name
Position
Company Address - Level 1, 47 Fernby Street, Carlow Qld 4072
Direct Phone
mobile
Email
Website -www.korvalit.com.au
Logo

Colors

Designer to choose colors to be used in the design.

Requirements
Must have
• Main Logo
• Cards will need to be editable to be able to personalize them for each new employee.
Nice to have
• The MapOut, ShipWell, KeepSteady would be okay to have if they can be sensibly and professionally added to the look without detracting from the main imagery.
• Maybe they could go on the back of the card? will leave this to your creative discretion as to whether/where they fit.
Should not have
• Should not have decorative or script fonts

```html
<!DOCTYPE html>
<html lang="en">
<head>
<meta charset="utf-8">
<title>korvalIT business card – front and back</title>
<link rel="stylesheet" href="https://fonts.googleapis.com/css2?family=Arimo:wght@400;700&display=swap">
<style>
  :root {
    --backdrop: #e3e3e3;
    --card: #f7f5f5;
    --brand-red: #b3161e;
    --label-red: #a3141b;
    --ink: #1e1e1e;
    --ink-soft: #3c3c3c;
    --pink-strong: rgba(232, 120, 128, 0.55);
    --pink-soft: rgba(240, 170, 175, 0.25);
    --map-green: #5a9e3c;
    --ship-blue: #2a86c8;
    --keep-magenta: #b0198a;
    --mark-dark: #2b2b2b;
  }
  * { box-sizing: border-box; margin: 0; padding: 0; }
  html, body { width: 1200px; height: 960px; overflow: hidden; }
  body {
    position: relative;
    background: var(--backdrop);
    font-family: "Arimo", Arial, sans-serif;
    color: var(--ink);
  }
  .card {
    position: absolute;
    width: 600px;
    height: 343px;
    background: var(--card);
    overflow: hidden;
    box-shadow: 0 2px 4px rgba(0,0,0,0.35);
  }
  .card--front { left: 315px; top: 113px; }
  .card--back  { left: 311px; top: 472px; }
  .card__pattern {
    position: absolute;
    inset: 0;
    background:
      radial-gradient(ellipse 70% 80% at 85% 0%, var(--pink-strong), transparent 70%),
      radial-gradient(ellipse 60% 70% at 35% 15%, var(--pink-soft), transparent 75%);
  }
  .wordmark {
    position: absolute;
    display: flex;
    align-items: center;
    gap: 12px;
    font-weight: 700;
    color: var(--mark-dark);
  }
  .wordmark__square {
    display: block;
    background: var(--brand-red);
  }
  .card--front .wordmark { right: 45px; top: 47px; font-size: 37px; letter-spacing: -0.5px; }
  .card--front .wordmark__square { width: 30px; height: 30px; }
  .person { position: absolute; left: 38px; top: 156px; }
  .person__name { font-size: 20px; font-weight: 700; color: var(--label-red); letter-spacing: 0.2px; }
  .person__role { font-size: 15px; margin-top: 2px; color: var(--ink); }
  .contact {
    position: absolute;
    left: 42px;
    top: 218px;
    list-style: none;
    font-size: 14px;
    line-height: 19px;
    color: var(--ink-soft);
  }
  .contact__label { font-weight: 700; color: var(--label-red); margin-right: 3px; }
  .website {
    position: absolute;
    right: 40px;
    top: 293px;
    font-size: 14px;
    color: var(--ink-soft);
  }
  .card--back .wordmark {
    left: 0; right: 0; top: 118px;
    justify-content: center;
    font-size: 56px;
    color: var(--brand-red);
  }
  .card--back .wordmark__square { width: 44px; height: 44px; }
  .services {
    position: absolute;
    left: 46px;
    top: 276px;
    display: flex;
    gap: 36px;
    list-style: none;
  }
  .service {
    display: flex;
    align-items: center;
    gap: 8px;
    font-size: 25px;
    font-weight: 700;
  }
  .service__square { width: 20px; height: 20px; display: block; }
  .service--map   { color: var(--map-green); }
  .service--ship  { color: var(--ship-blue); }
  .service--keep  { color: var(--keep-magenta); }
  .service--map .service__square  { background: var(--map-green); }
  .service--ship .service__square { background: var(--ship-blue); }
  .service--keep .service__square { background: var(--keep-magenta); }
</style>
</head>
<body>
  <section class="card card--front">
    <div class="card__pattern" role="img" aria-label="Soft pink pattern of overlapping squares and dots"></div>
    <div class="wordmark"><span class="wordmark__square"></span>korvalIT</div>
    <div class="person">
      <p class="person__name">DANA WHITFORD</p>
      <p class="person__role">Business Development Manager</p>
    </div>
    <ul class="contact">
      <li><span class="contact__label">P:</span>+61 (0)7 3840 5120</li>
      <li><span class="contact__label">P:</span>+61 (0)7 3840 5127</li>
      <li><span class="contact__label">C:</span>+61 (0)412 630 948</li>
      <li><span class="contact__label">F:</span>+61 (0)7 3840 5199</li>
      <li><span class="contact__label">E:</span>dwhitford@korvalit.com.au</li>
    </ul>
    <p class="website">www.korvalit.com.au</p>
  </section>

  <section class="card card--back">
    <div class="card__pattern" role="img" aria-label="Soft pink pattern of overlapping squares and dots"></div>
    <div class="wordmark"><span class="wordmark__square"></span>korvalIT</div>
    <ul class="services">
      <li class="service service--map"><span class="service__square"></span>MapOut</li>
      <li class="service service--ship"><span class="service__square"></span>ShipWell</li>
      <li class="service service--keep"><span class="service__square"></span>KeepSteady</li>
    </ul>
  </section>
</body>
</html>
```